Business card for a new cabinet shop company named Veloran Cabinets for high end cabinets

Design a business card, thinking dark rich green with colours to speak of high end luxury ie; cream, gold, black possibly

Mitchell Tarrowby
Director Craftsman
Email: info@veloranjoinery-example.com.au
Instagram : @veloran.cabinets

```html
<!DOCTYPE html>
<html lang="en">
<head>
<meta charset="utf-8">
<title>Veloran Cabinets – Business Card</title>
<link href="https://fonts.googleapis.com/css2?family=Montserrat:wght@400;500;700&display=swap" rel="stylesheet">
<style>
  :root {
    --stage: #2b2b2b;
    --card: #030a06;
    --card-edge: #0b140e;
    --gold: #c9a24e;
    --cream: #e8e2d0;
    --pattern-a: #050c08;
    --pattern-b: #141c17;
  }
  * { box-sizing: border-box; margin: 0; padding: 0; }
  html, body {
    width: 1200px; height: 875px; overflow: hidden;
    background: var(--stage);
    font-family: "Montserrat", Arial, sans-serif;
  }
  .stage {
    position: relative; width: 1200px; height: 875px;
    display: flex; flex-direction: column; align-items: center; justify-content: center; gap: 56px;
  }
  .card {
    position: relative; width: 600px; height: 343px;
    background: var(--card);
    border-radius: 22px;
    border: 1px solid var(--card-edge);
    border-bottom: 2px solid var(--gold);
    box-shadow: 0 18px 40px rgba(0,0,0,.45);
    overflow: hidden;
  }

  /* back side */
  .card-back .pattern-field {
    position: absolute; inset: 0;
    background:
      repeating-linear-gradient(-30deg, transparent 0 38px, rgba(255,255,255,.025) 38px 40px),
      radial-gradient(ellipse at 25% 75%, var(--pattern-b), var(--pattern-a) 75%);
  }
  .card-back .back-brand {
    position: absolute; inset: 0;
    display: flex; align-items: center; justify-content: center; gap: 12px;
  }
  .back-brand .brand-dot { background: var(--gold); }
  .back-brand .brand-name { color: var(--gold); }

  /* shared brand lockup */
  .brand { display: flex; align-items: center; gap: 12px; }
  .brand-dot { width: 12px; height: 12px; border-radius: 50%; background: var(--cream); flex: none; }
  .brand-name {
    color: var(--cream); font-weight: 500; font-size: 22px; letter-spacing: .04em; white-space: nowrap;
  }

  /* front side */
  .card-front .front-layout {
    position: absolute; inset: 0;
    display: flex; align-items: center; justify-content: center; gap: 24px;
    padding: 0 44px;
  }
  .divider { width: 1.5px; height: 118px; background: var(--gold); flex: none; }
  .contact { white-space: nowrap; }
  .person-name {
    color: var(--gold); font-weight: 700; font-size: 18px; line-height: 1.1; letter-spacing: .01em;
  }
  .person-title {
    color: var(--cream); font-size: 12.5px; font-weight: 500; margin-top: 5px; letter-spacing: .02em;
  }
  .details { list-style: none; margin-top: 20px; }
  .details li {
    display: flex; align-items: center; gap: 9px;
    color: var(--cream); font-size: 11px; line-height: 1; margin-bottom: 11px;
  }
  .details li:last-child { margin-bottom: 0; }
  .details svg { flex: none; }
</style>
</head>
<body>
<main class="stage">
  <section class="card card-back" aria-label="Card back">
    <div class="pattern-field" role="img" aria-label="Repeating tonal brand pattern on dark green-black"></div>
    <div class="brand back-brand">
      <span class="brand-dot"></span>
      <span class="brand-name">Veloran Cabinets</span>
    </div>
  </section>

  <section class="card card-front" aria-label="Card front">
    <div class="front-layout">
      <div class="brand">
        <span class="brand-dot"></span>
        <span class="brand-name">Veloran Cabinets</span>
      </div>
      <div class="divider"></div>
      <div class="contact">
        <h1 class="person-name">MITCHELL TARROWBY</h1>
        <p class="person-title">Director Craftsman</p>
        <ul class="details">
          <li>
            <svg width="14" height="10" viewBox="0 0 14 10" aria-hidden="true">
              <rect x="0.5" y="0.5" width="13" height="9" fill="var(--gold)"/>
              <path d="M0.5 0.5 L7 5.5 L13.5 0.5" fill="none" stroke="var(--card)" stroke-width="1.2"/>
            </svg>
            info@veloranjoinery-example.com.au
          </li>
          <li>
            <svg width="14" height="14" viewBox="0 0 14 14" aria-hidden="true">
              <circle cx="7" cy="7" r="5.5" fill="none" stroke="var(--gold)" stroke-width="1.5"/>
            </svg>
            @veloran.cabinets
          </li>
        </ul>
      </div>
    </div>
  </section>
</main>
</body>
</html>
```